Quiet Hollow is a cabin in Gatlinburg, Tennessee, near the Ferncrest Ridge National Park. When our cabin was built, there was one thing more important than any other--peace. The front of our cabin is surrounded by woods. It has a huge deck with a swing, Adirondack chairs, and a love seat for relaxation. The back deck has a hot tub, a large round glass table for cocktails or dinner, and because we left no stone unturned, we have a telescope for stargazing. There are two master suites, each have a private bath with a large jetted tub, seperate shower, flat screen TV, and a door that leads to the back deck.

Industry/Entity Type

Business

Contact Information for Business Card

Quiet Hollow Vacation Rentals, LLC
871 Belford Crest Pl.
Oakland, Ky 42159
Janet M. Pruitt, Owner/Manager
(270) 614.2087

```html
<!DOCTYPE html>
<html lang="en">
<head>
<meta charset="utf-8">
<title>Quiet Hollow Vacation Rentals — Business Card</title>
<link href="https://fonts.googleapis.com/css2?family=Source+Sans+3:wght@400;600;700&display=swap" rel="stylesheet">
<style>
  :root {
    --backdrop: #151515;
    --card-white: #ffffff;
    --card-green: #2aad4a;
    --navy: #1b2f8e;
    --leaf: #22843a;
    --icon: #2a8a3e;
    --mark-blue: #2445b0;
  }
  * { margin: 0; padding: 0; box-sizing: border-box; }
  html, body {
    width: 1200px; height: 900px; overflow: hidden;
    background: var(--backdrop);
    font-family: "Source Sans 3", "Myriad Pro", Arial, sans-serif;
  }
  .stage { position: relative; width: 1200px; height: 900px; }
  .card { position: absolute; border-radius: 12px; overflow: hidden; }
  .card--front { left: 155px; top: 311px; width: 429px; height: 248px; background: var(--card-white); }
  .card--back { left: 629px; top: 312px; width: 432px; height: 250px; background: var(--card-green); }

  .brand-front {
    position: absolute; left: 32px; top: 122px; width: 160px;
    display: flex; align-items: center; gap: 6px;
    font-size: 19px; font-weight: 700; color: var(--navy);
    white-space: nowrap;
  }
  .brand-front .dot { width: 9px; height: 9px; border-radius: 50%; background: var(--leaf); flex: none; }

  .details { position: absolute; left: 207px; top: 48px; width: 212px; color: var(--navy); }
  .person-name { font-size: 19px; font-weight: 700; line-height: 1; white-space: nowrap; }
  .person-role { font-size: 13px; color: var(--leaf); margin-top: 5px; line-height: 1; }
  .address { font-size: 13px; line-height: 14px; margin-top: 12px; }
  .contact-list { list-style: none; margin-top: 13px; font-size: 13px; line-height: 16.3px; }
  .contact-list li { display: flex; align-items: center; gap: 7px; white-space: nowrap; }
  .contact-list svg { width: 9px; height: 9px; flex: none; fill: var(--icon); }

  .brand-back {
    position: absolute; left: 0; right: 0; top: 106px; text-align: center;
    font-size: 30px; font-weight: 700; color: var(--mark-blue);
  }
</style>
</head>
<body>
<main class="stage">
  <section class="card card--front" aria-label="Business card front">
    <div class="brand-front"><span class="dot"></span>Quiet Hollow</div>
    <div class="details">
      <h1 class="person-name">Janet M. Pruitt</h1>
      <p class="person-role">Owner/Manager</p>
      <p class="address">871 Belford Crest Pl.<br>Oakland, Ky 42159</p>
      <ul class="contact-list">
        <li><svg viewBox="0 0 10 10"><rect x="2.5" y="0" width="5" height="10" rx="1"/><rect x="3.5" y="1.5" width="3" height="6" fill="#fff"/></svg>(270) 614.2087</li>
        <li><svg viewBox="0 0 10 10"><rect x="0" y="2" width="10" height="6.5" rx="1"/><path d="M0.5 2.5 L5 6 L9.5 2.5" stroke="#fff" stroke-width="1" fill="none"/></svg>stay@quiethollowrentals.com</li>
        <li><svg viewBox="0 0 10 10"><path d="M2 8 L8 2" stroke="#2a8a3e" stroke-width="2" stroke-linecap="round"/></svg>www.quiethollowrentals.com</li>
      </ul>
    </div>
  </section>

  <section class="card card--back" aria-label="Business card back">
    <div class="brand-back">Quiet Hollow</div>
  </section>
</main>
</body>
</html>
```